Meadow Paw Web Site

We have basically a start up business that I need help with. This project is just for the web site.

Our product is a frozen raw pet food that promotes weight control, less shedding, smaller stools and an overall better health. The product is in nugget form similar to what you would see in a steak shish kabob. I only share that with you in case you want to incorporate that in the design.

We have been in business for 17 years but all of our sales have been word of mouth. We are going to be launching an infomercial this summer and I need everything stated previously to be completed before we can launch the infomercial.

We need the following (6) pages:

Home:
This is where we need to have the ability to purchase our products. Our main goal is to get the consumer to purchase our product. We have our own shopping cart so we just need to allow for the insertion of that shopping cart.

Why Raw:
This will just be a page with 4-5 paragraphs and an embedded YouTube video.

How to Use:
We will need a page with a chart (4 Columns wide with 6 rows) as well as an embedded YouTube video.

Customer Success Stories:
Allow us to add these as we move forward. I need a placeholder for an image of the customers pet and a paragraph or two explaining the situation

Where to Buy:
- Online - Find a Retailer - Find a Local Distributor - Call to Order

Contact Us:
Copper Ridge Holdings, Inc.
2740 Copper Rd
Eagan, MN 55148
(800) 555-0148

We need to provide links to our to be created... Facebook page, Twitter Account, Youtube Channel, Google circle, Blog
Updates

All, I have received many front page designs that look good.  Please notice in the brief that I need multiple pages built not just the home page.  

Thanks,

Dale

Reason: I need to see the rest of the pages. Thanks, Dale

Target Market(s)

Women between the ages of 30 & 60.

Industry/Entity Type

Shopping

```html
<!DOCTYPE html>
<html lang="en">
<head>
<meta charset="utf-8">
<title>Meadow Paw — Success Stories</title>
<link href="https://fonts.googleapis.com/css2?family=Open+Sans:wght@400;600;700;800&display=swap" rel="stylesheet">
<style>
  :root{
    --orange:#e8731a;
    --orange-dark:#c85a0c;
    --orange-light:#f39a3c;
    --yellow:#f7c21c;
    --brown:#3a2a1e;
    --ink:#333333;
    --text:#5d5d5d;
    --muted:#8a8a8a;
    --page:#f1f1f1;
    --card:#ffffff;
    --rule:#dcdcdc;
    --footer:#2b2b2b;
    --footer-deep:#1d1d1d;
    --footer-text:#a9a9a9;
  }
  *{box-sizing:border-box;margin:0;padding:0}
  html,body{width:813px;height:1200px;overflow:hidden}
  body{font-family:"Open Sans",Arial,sans-serif;background:var(--page);color:var(--ink);position:relative}

  /* header */
  .site-header{position:absolute;left:0;top:0;width:813px;height:108px;background:#fff}
  .brand{position:absolute;left:80px;top:18px;display:flex;align-items:center;gap:10px}
  .brand-mark{width:36px;height:36px;background:var(--brown)}
  .brand-name{font-size:22px;font-weight:800;color:var(--orange);letter-spacing:-.3px}
  .account-links{position:absolute;right:81px;top:12px;font-size:9px;font-weight:700;color:var(--orange);letter-spacing:.3px;white-space:nowrap}
  .account-links span{margin:0 5px;color:var(--muted);font-weight:400}
  .auth{position:absolute;right:87px;top:40px;display:flex;gap:8px}
  .btn{display:inline-block;font-size:10px;font-weight:700;padding:4px 12px;border-radius:3px;color:#fff}
  .btn-signin{background:var(--orange)}
  .btn-register{background:var(--yellow);color:var(--brown)}
  .cart{position:absolute;left:440px;top:81px;display:flex;align-items:center;gap:5px;font-size:8.5px;font-weight:700;color:var(--ink);white-space:nowrap}
  .cart .count{color:var(--orange);margin-left:4px}
  .search{position:absolute;left:598px;top:77px;width:134px;height:22px;border:1px solid var(--rule);border-radius:11px;background:#fafafa;font-size:9px;color:var(--muted);padding:4px 10px}
  .search svg{position:absolute;right:7px;top:5px}

  /* nav */
  .main-nav{position:absolute;left:81px;top:112px;width:651px;height:36px;background:linear-gradient(var(--orange-light),var(--orange));display:flex;border-radius:2px}
  .nav-home{width:58px;height:36px;background:var(--brown);display:flex;align-items:center;justify-content:center}
  .nav-item{flex:1;display:flex;align-items:center;justify-content:center;font-size:12px;font-weight:700;color:#fff;border-left:1px solid rgba(255,255,255,.35);white-space:nowrap}

  /* content */
  .page-title{position:absolute;left:86px;top:172px;width:641px;font-size:17px;font-weight:800;letter-spacing:.2px;padding-bottom:8px;border-bottom:1px solid var(--rule)}
  .page-title .accent{color:var(--orange)}
  .stories{position:absolute;left:86px;top:216px;width:641px}
  .story{height:172px;margin-bottom:18px;background:var(--card);box-shadow:0 1px 3px rgba(0,0,0,.15);display:flex;padding:6px}
  .story-photo{width:182px;height:160px;flex:none}
  .story-body{position:relative;padding:10px 16px 0 44px;flex:1}
  .quote-open{position:absolute;left:18px;top:2px;font-size:40px;font-weight:800;color:var(--orange);line-height:1;font-family:Georgia,serif}
  .story-text{font-size:10.5px;line-height:15.5px;color:var(--text)}
  .quote-close{font-size:34px;font-weight:800;color:var(--orange);line-height:.5;font-family:Georgia,serif;vertical-align:-14px;margin-left:4px}
  .story-author{position:absolute;right:18px;bottom:6px;font-size:10.5px;font-weight:700;color:var(--ink)}

  /* footer */
  .site-footer{position:absolute;left:0;top:986px;width:813px;height:190px;background:var(--footer);padding:22px 81px 0;display:flex;gap:18px}
  .footer-col{width:85px;flex:none}
  .footer-col.products{width:88px}
  .footer-col.buy{width:107px}
  .footer-col.contact{width:137px}
  .footer-col h4{font-size:11px;font-weight:700;color:#fff;margin-bottom:10px;white-space:nowrap}
  .footer-col li{list-style:none;font-size:8.5px;line-height:14px;color:var(--footer-text);white-space:nowrap}
  .footer-col p{font-size:8.5px;line-height:13px;color:var(--footer-text)}
  .footer-col.newsletter{width:162px}
  .news-input{margin-top:8px;height:18px;width:100%;background:#fff;border-radius:2px;font-size:8px;color:var(--muted);padding:3px 6px}
  .news-btn{margin-top:6px;margin-left:auto;width:56px;height:18px;background:var(--orange);color:#fff;font-size:8.5px;font-weight:700;text-align:center;line-height:18px;border-radius:2px}
  .socials{display:flex;gap:4px;margin-top:8px}
  .socials i{display:block;width:15px;height:15px;border-radius:2px}
  .bottom-bar{position:absolute;left:0;top:1176px;width:813px;height:24px;background:var(--footer-deep);font-size:8.5px;color:var(--footer-text);padding:6px 81px}
</style>
</head>
<body>

<header class="site-header">
  <div class="brand"><span class="brand-mark"></span><span class="brand-name">Meadow Paw</span></div>
  <div class="account-links">MY ACCOUNT<span>|</span>WISH LIST<span>|</span>MY CART<span>|</span>CHECKOUT</div>
  <div class="auth"><span class="btn btn-signin">Sign in</span><span class="btn btn-register">Register</span></div>
  <div class="cart">
    <svg width="16" height="14" viewBox="0 0 16 14"><path d="M1 1h3l2 8h8l1.5-6H5" fill="none" stroke="#e8731a" stroke-width="1.6"/><circle cx="7" cy="12" r="1.3" fill="#e8731a"/><circle cx="13" cy="12" r="1.3" fill="#e8731a"/></svg>
    SHOPPING CART<span class="count">(33 ITEMS)</span>
  </div>
  <div class="search">Search...
    <svg width="11" height="11" viewBox="0 0 11 11"><circle cx="4.5" cy="4.5" r="3.5" fill="none" stroke="#e8731a" stroke-width="1.5"/><path d="M7 7l3 3" stroke="#e8731a" stroke-width="1.5"/></svg>
  </div>
</header>

<nav class="main-nav">
  <div class="nav-home">
    <svg width="16" height="14" viewBox="0 0 16 14"><path d="M8 1L1 7h2v6h4V9h2v4h4V7h2z" fill="#fff"/></svg>
  </div>
  <div class="nav-item">Why Raw</div>
  <div class="nav-item">How to Use</div>
  <div class="nav-item">Where to Buy</div>
  <div class="nav-item">Success Stories</div>
  <div class="nav-item">Contact Us</div>
</nav>

<h1 class="page-title"><span class="accent">SUCCESS</span> STORIES</h1>

<main class="stories">
  <article class="story">
    <div class="story-photo" role="img" aria-label="Customer smiling with her small dog" style="background:linear-gradient(135deg,#d9c3ad,#8a6a52)"></div>
    <div class="story-body">
      <span class="quote-open">“</span>
      <p class="story-text">Lorem ipsum dolor sit amet, consectetur adipiscing elit. Nulla ornare, nisi et interdum condimentum, felis lectus pharetra nunc, nec tristique quam mi eu risus. Nullam ornare sagittis ante, id sollicitudin nunc. Vestibulum id sodales nisi. Pellentesque nunc dolor, faucibus in erat a, hendrerit mattis elit. Duis ornare mi at risus egestas malesuada.<span class="quote-close">”</span></p>
      <span class="story-author">– Client Name Here</span>
    </div>
  </article>
  <article class="story">
    <div class="story-photo" role="img" aria-label="Couple sitting with their dog" style="background:linear-gradient(135deg,#e8e2d8,#b49778)"></div>
    <div class="story-body">
      <span class="quote-open">“</span>
      <p class="story-text">Lorem ipsum dolor sit amet, consectetur adipiscing elit. Nulla ornare, nisi et interdum condimentum, felis lectus pharetra nunc, nec tristique quam mi eu risus. Nullam ornare sagittis ante, id sollicitudin nunc. Vestibulum id sodales nisi. Pellentesque nunc dolor, faucibus in erat a, hendrerit mattis elit. Duis ornare mi at risus egestas malesuada.<span class="quote-close">”</span></p>
      <span class="story-author">– Client Name Here</span>
    </div>
  </article>
  <article class="story">
    <div class="story-photo" role="img" aria-label="Man close to his dog" style="background:linear-gradient(135deg,#d8c9b4,#8f7a63)"></div>
    <div class="story-body">
      <span class="quote-open">“</span>
      <p class="story-text">Lorem ipsum dolor sit amet, consectetur adipiscing elit. Nulla ornare, nisi et interdum condimentum, felis lectus pharetra nunc, nec tristique quam mi eu risus. Nullam ornare sagittis ante, id sollicitudin nunc. Vestibulum id sodales nisi. Pellentesque nunc dolor, faucibus in erat a, hendrerit mattis elit. Duis ornare mi at risus egestas malesuada.<span class="quote-close">”</span></p>
      <span class="story-author">– Client Name Here</span>
    </div>
  </article>
  <article class="story">
    <div class="story-photo" role="img" aria-label="Woman hugging her golden dog" style="background:linear-gradient(135deg,#eadcc4,#c2925a)"></div>
    <div class="story-body">
      <span class="quote-open">“</span>
      <p class="story-text">Lorem ipsum dolor sit amet, consectetur adipiscing elit. Nulla ornare, nisi et interdum condimentum, felis lectus pharetra nunc, nec tristique quam mi eu risus. Nullam ornare sagittis ante, id sollicitudin nunc. Vestibulum id sodales nisi. Pellentesque nunc dolor, faucibus in erat a, hendrerit mattis elit. Duis ornare mi at risus egestas malesuada.<span class="quote-close">”</span></p>
      <span class="story-author">– Client Name Here</span>
    </div>
  </article>
</main>

<footer class="site-footer">
  <div class="footer-col">
    <h4>Quick Links</h4>
    <ul><li>Why Raw</li><li>How to Use</li><li>Where to Buy</li><li>Success Stories</li><li>How to Use</li><li>Where to Buy</li><li>Contact Us</li></ul>
  </div>
  <div class="footer-col products">
    <h4>Top Products</h4>
    <ul><li>Product 1</li><li>Product 2</li><li>Product 3</li><li>Product 4</li><li>Product 5</li><li>Product 6</li><li>Product 7</li></ul>
  </div>
  <div class="footer-col buy">
    <h4>Where to Buy</h4>
    <ul><li>Find a Retailer</li><li>Find a Local Distributor</li><li>Call to Order</li></ul>
  </div>
  <div class="footer-col contact">
    <h4>Contact Information</h4>
    <p>COPPER RIDGE HOLDINGS, INC.<br>2740 Copper Rd<br>Eagan, MN 55148</p>
    <p style="margin-top:8px">Tel: (800) 555-0148</p>
  </div>
  <div class="footer-col newsletter">
    <h4>Newsletter</h4>
    <p>Stay connected with a handful of recent updates and news.</p>
    <div class="news-input">Email address</div>
    <div class="news-btn">Subscribe</div>
    <div class="socials">
      <i style="background:#3b5b98"></i><i style="background:#3fa9e0"></i><i style="background:#c4302b"></i><i style="background:#d34836"></i><i style="background:#e8731a"></i>
    </div>
  </div>
</footer>
<div class="bottom-bar">Copyright © 2013 Meadow Paw | Privacy Policy</div>

</body>
</html>
```